Website Design for The Elder Nook

Please design and code a new website.
Here are the sites I like best:
http://www.voyaglint.com/alternate/
http://www.wheelgiftbay.org
Please make it similar but look at the competitor site (below) for images and wording. This is NOT a car donation site. It's a senior lead placement site like https://www.kinhavenfinder.com. I just like this sites above as a lead generation sites.
Competitor site:
https://www.kinhavenfinder.com (use ideas / verbiage from this site)
Updates
Competitor site:
Coding
Coded - Design and coding required
Number of Pages Required
1 page
Look and feel
Each slider illustrates characteristics of the customer's brand and the style your logo design should communicate.

```html
<!DOCTYPE html>
<html lang="en">
<head>
<meta charset="utf-8">
<title>The Elder Nook</title>
<link rel="stylesheet" href="https://fonts.googleapis.com/css2?family=Poppins:wght@300;400;500;600&family=Open+Sans:wght@400;600&display=swap">
<style>
:root{
  --blue:#0d4a8f;
  --blue-dark:#083a73;
  --orange:#f0a623;
  --orange-soft:#e9a637;
  --page:#e6e6e6;
  --white:#fff;
  --text:#333;
  --muted:#666;
  --faq:#f0f0f0;
}
*{margin:0;padding:0;box-sizing:border-box}
html,body{width:1200px;height:2304px;overflow:hidden;background:var(--page)}
body{font-family:"Open Sans",sans-serif;color:var(--text)}
.site{position:absolute;left:157px;top:0;width:885px;height:2304px;background:var(--white)}
.abs{position:absolute}
.header{left:0;top:0;width:885px;height:76px}
.brand{left:15px;top:14px;font-family:"Poppins",sans-serif;font-weight:500;font-size:37px;color:var(--blue);line-height:1}
.phone{right:15px;top:25px;font-family:"Poppins",sans-serif;font-weight:300;font-size:18px;color:#555;display:flex;align-items:center;gap:6px}
.nav{left:0;top:76px;width:885px;height:37px;background:var(--blue);display:flex;font-family:"Poppins",sans-serif;font-size:12.5px;color:#cfdcec}
.nav span{display:flex;align-items:center;padding:0 22px;height:37px}
.nav .active{background:var(--blue-dark);color:#fff}
.hero{left:0;top:113px;width:885px;height:463px;background:linear-gradient(100deg,#cfcac3 0%,#a89d91 35%,#8d8378 55%,#b9b2a6 80%,#d9d5ce 100%)}
.hero-copy{right:38px;top:16px;text-align:right;font-family:"Poppins",sans-serif}
.hero-copy h1{font-size:23px;font-weight:600;color:var(--blue);line-height:31px}
.hero-copy p{font-size:14.5px;color:#222;margin-top:4px}
.lead-form{left:592px;top:104px;width:255px;height:337px;background:var(--orange);padding:15px 15px}
.field{width:225px;height:37px;background:#fff;margin-bottom:8px;font-size:11.5px;color:#222;padding:11px 14px}
.submit{width:225px;height:37px;background:var(--blue);color:#fff;font-family:"Poppins",sans-serif;font-size:14px;display:flex;align-items:center;justify-content:center}
.arrow{top:218px;width:23px;height:30px;background:rgba(40,40,40,.75);display:flex;align-items:center;justify-content:center}
h2{font-family:"Poppins",sans-serif;font-weight:400;text-align:center;color:var(--blue)}
.support h2{font-size:28px;position:absolute;left:0;width:885px;top:644px}
.support p{position:absolute;left:20px;width:845px;top:685px;font-size:11.6px;line-height:19.5px;text-align:center;color:#444}
.features{left:0;top:768px;width:885px;display:flex}
.feature{width:177px;text-align:center;color:var(--blue);font-size:11.8px;line-height:16.5px}
.feature svg{display:block;margin:0 auto 10px;height:40px}
.reviews{left:0;top:923px;width:885px;height:464px;background:linear-gradient(90deg,#e9a12a,#f0ab3a 50%,#e79f28)}
.reviews h2{position:absolute;left:0;width:885px;top:48px;color:#fff;font-size:27px}
.card{top:95px;width:274px;height:280px;background:#fff;text-align:center;padding:21px 16px 0;font-family:"Poppins",sans-serif}
.card q{display:block;font-size:12.6px;font-weight:300;line-height:22.4px;color:#333;height:135px}
.avatar{width:74px;height:74px;border-radius:50%;margin:0 auto;background:radial-gradient(circle at 50% 40%,#e3cdbb,#b9a79a 60%,#ecebeb)}
.card b{display:block;font-weight:400;color:var(--blue);font-size:14px;margin-top:4px}
.card small{display:block;font-family:"Open Sans",sans-serif;font-size:9.5px;color:#666;margin-top:1px}
.dots{left:0;width:885px;top:400px;display:flex;justify-content:center;gap:11px}
.dots i{width:11px;height:11px;border-radius:50%;background:#8a5a0d}
.dots i.on{background:#fff}
.tile{top:1462px;width:274px}
.tile .photo{height:180px}
.tile .label{height:38px;background:var(--blue);color:#fff;font-family:"Poppins",sans-serif;font-size:14px;display:flex;align-items:center;justify-content:center}
.faq h2{position:absolute;left:0;width:885px;top:1724px;font-size:27px}
.qa{left:15px;width:855px;background:var(--faq);font-family:"Poppins",sans-serif}
.qa .q{position:absolute;left:52px;font-size:17px;font-weight:300;color:#555}
.qa .box{position:absolute;left:22px;width:13px;height:13px}
.qa.open .q{color:var(--blue);font-weight:400}
.qa .a{position:absolute;left:53px;top:48px;width:770px;font-family:"Open Sans",sans-serif;font-size:10.2px;line-height:18px;color:#444}
.footer{left:0;top:2214px;width:885px;height:90px;background:var(--blue);color:#dfe8f3;font-size:9.7px}
.footer .links{position:absolute;left:16px;top:28px;word-spacing:1px}
.footer .copy{position:absolute;left:16px;top:55px}
.social{position:absolute;top:32px;width:16px;height:16px;border-radius:50%;background:#b8cbe2}
</style>
</head>
<body>
<div class="site">
  <header class="abs header">
    <div class="abs brand">The Elder Nook</div>
    <div class="abs phone">
      <svg width="13" height="13" viewBox="0 0 24 24"><path fill="#666" d="M6.6 10.8a15 15 0 0 0 6.6 6.6l2.2-2.2c.3-.3.7-.4 1-.2 1.1.4 2.3.6 3.6.6.6 0 1 .4 1 1V20c0 .6-.4 1-1 1A17 17 0 0 1 3 4c0-.6.4-1 1-1h3.5c.6 0 1 .4 1 1 0 1.3.2 2.5.6 3.6.1.3 0 .7-.2 1z"/></svg>
      555 210 4837
    </div>
  </header>
  <nav class="abs nav">
    <span class="active">Assisted Living</span>
    <span>Memory Care</span>
    <span>Nursing Homes</span>
    <span>More Living Options&nbsp;▾</span>
    <span>Planning &amp; Advice</span>
    <span>How Our Service Works</span>
  </nav>
  <section class="abs hero" role="img" aria-label="Photo of a young caregiver helping an older man in a wheelchair">
    <div class="abs hero-copy">
      <h1>You know your family.<br>We know Senior Living.</h1>
      <p>Find Senior Living Near You.</p>
    </div>
    <div class="abs lead-form">
      <div class="field">Name</div>
      <div class="field">Email</div>
      <div class="field">Phone</div>
      <div class="field">Address</div>
      <div class="field">City</div>
      <div class="field">Zipcode</div>
      <div class="submit">SUBMIT</div>
    </div>
    <div class="abs arrow" style="left:0"><svg width="10" height="18" viewBox="0 0 10 18"><path d="M9 1 1 9l8 8" fill="none" stroke="#fff" stroke-width="1.3"/></svg></div>
    <div class="abs arrow" style="right:0"><svg width="10" height="18" viewBox="0 0 10 18"><path d="m1 1 8 8-8 8" fill="none" stroke="#fff" stroke-width="1.3"/></svg></div>
  </section>

  <section class="support">
    <h2>The support you need to make the right choice</h2>
    <p>Etiam sit amet velit ut nibh ullamcorper rhoncus vel vitae risus. In condimentum purus libero, non pellentesque dui blandit quis. Duis rutrum venenatis tristique. Nam vitae placerat dui, nec sagittis sem. Aliquam a lacus in enim viverra congue. Aliquam interdum tortor erat, eget porta elit molestie et. Aenean tortor magna, iaculis vitae condimentum vitae, laoreet eget erat. Praesent sollicitudin, justo quis faucibus dapibus.</p>
    <div class="abs features">
      <div class="feature"><svg viewBox="0 0 40 40" width="40"><circle cx="20" cy="12" r="9" fill="var(--blue)"/><path d="M3 38c0-10 7-15 17-15s17 5 17 15z" fill="var(--blue)"/></svg>Quisque venenatis viverra<br>leo eu vulputate</div>
      <div class="feature"><svg viewBox="0 0 44 40" width="44"><path d="M22 3 2 20l3 3 17-14 17 14 3-3z" fill="var(--blue)"/><path d="M8 21v16h10v-10h8v10h10V21L22 10z" fill="var(--blue)"/></svg>Fusce aliquet efficitur<br>auctor</div>
      <div class="feature"><svg viewBox="0 0 40 44" width="36"><rect x="2" y="6" width="36" height="36" rx="3" fill="var(--blue)"/><rect x="9" y="1" width="4" height="9" fill="var(--blue)"/><rect x="27" y="1" width="4" height="9" fill="var(--blue)"/><g fill="#fff"><rect x="7" y="17" width="6" height="6"/><rect x="17" y="17" width="6" height="6"/><rect x="27" y="17" width="6" height="6"/><rect x="7" y="28" width="6" height="6"/><rect x="17" y="28" width="6" height="6"/><rect x="27" y="28" width="6" height="6"/></g></svg>Aenean mattis volutpat<br>massa</div>
      <div class="feature"><svg viewBox="0 0 40 44" width="36"><path d="M6 3v14a10 10 0 0 0 20 0V3" fill="none" stroke="var(--blue)" stroke-width="5"/><path d="M16 27v6a8 8 0 0 0 16 0v-10" fill="none" stroke="var(--blue)" stroke-width="4"/><circle cx="32" cy="18" r="5" fill="var(--blue)"/></svg>Vivamus hendrerit<br>maximus tempus</div>
      <div class="feature"><svg viewBox="0 0 48 30" width="48" style="height:30px;margin-top:6px;margin-bottom:14px"><rect x="1" y="1" width="46" height="28" fill="var(--blue)"/><circle cx="24" cy="15" r="8" fill="#fff"/><text x="24" y="19.5" text-anchor="middle" font-family="Poppins,sans-serif" font-size="12" font-weight="600" fill="var(--blue)">1</text></svg>Proin efficitur sem nec<br>imperdiet</div>
    </div>
  </section>

  <section class="abs reviews" role="img" aria-label="Warm orange-tinted photo of a caregiver laughing with a senior">
    <h2>97% of our customers recommend our service</h2>
    <div class="abs card" style="left:15px"><q>“ Suspendisse volutpat ligula turpis. In elementum purus sed ante ultricies, ac aliquam ante dignissim. In hac habitasse platea dictumst. In id euismod lorem. Nulla diam purus. ”</q><div class="avatar" role="img" aria-label="Portrait of a smiling older man with glasses"></div><b>Ray Dunmore</b><small>Vestibulum ultrices amet</small></div>
    <div class="abs card" style="left:305px"><q>“ Duis rutrum venenatis tristique. Nam vitae placerat dui, nec sagittis sem. Aliquam a lacus in enim viverra congue. Aliquam interdum tortor erat, eget porta elit molestie et. ”</q><div class="avatar" role="img" aria-label="Portrait of a smiling grey-haired man"></div><b>Michael</b><small>Vestibulum ultrices amet</small></div>
    <div class="abs card" style="left:595px"><q>“ Maecenas mattis sem urna, sed pharetra enim pretium a. Suspendisse volutpat ligula turpis. In elementum purus sed ante ultricies, ac aliquam ante dignissim. ”</q><div class="avatar" role="img" aria-label="Portrait of a smiling senior man"></div><b>Daniel</b><small>Vestibulum ultrices amet</small></div>
    <div class="abs dots"><i class="on"></i><i></i><i></i><i></i></div>
  </section>

  <div class="abs tile" style="left:15px"><div class="photo" role="img" aria-label="Photo of a happy senior man in a plaid shirt at home" style="background:linear-gradient(160deg,#d9d4cc,#a7948a 55%,#c8c2bb)"></div><div class="label">INDEPENDENT LIVING</div></div>
  <div class="abs tile" style="left:305px"><div class="photo" role="img" aria-label="Photo of a senior man with a cane beside a smiling younger woman" style="background:linear-gradient(160deg,#d6d8d2,#a99a8b 50%,#b8c6cf)"></div><div class="label">MEMORY CARE</div></div>
  <div class="abs tile" style="left:595px"><div class="photo" role="img" aria-label="Photo of a nurse helping an older man sit up in bed" style="background:linear-gradient(160deg,#d6e1e4,#8fb3cc 50%,#c7a99a)"></div><div class="label">NURSING HOMES</div></div>

  <section class="faq">
    <h2>Frequently Asked Questions</h2>
    <div class="abs qa open" style="top:1782px;height:123px">
      <svg class="box" style="top:25px" viewBox="0 0 13 13"><rect width="13" height="13" rx="2" fill="var(--blue)"/><rect x="3" y="5.7" width="7" height="1.6" fill="#fff"/></svg>
      <div class="q" style="top:18px">Maecenas sed nibh sed nisi tristique pharetra?</div>
      <div class="a">Nullam varius, orci nec porttitor cursus, eros diam viverra sapien, a convallis mauris augue eget erat. Sed efficitur lorem vel est rhoncus rutrum. Suspendisse porttitor auctor vehicula. In sodales sem a lectus viverra, vitae varius nisi sodales. Aliquam cursus dolor vel interdum pellentesque. Fusce convallis venenatis pulvinar. Curabitur vel dapibus tellus. Vivamus dolor sapien, sollicitudin nec pulvinar sit amet, vulputate at elit.</div>
    </div>
    <div class="abs qa" style="top:1909px;height:60px"><svg class="box" style="top:24px" viewBox="0 0 13 13"><rect width="13" height="13" rx="2" fill="#666"/><path d="M3 6.5h7M6.5 3v7" stroke="#fff" stroke-width="1.6"/></svg><div class="q" style="top:17px">Donec aliquam quam eget euismod dictum?</div></div>
    <div class="abs qa" style="top:1973px;height:60px"><svg class="box" style="top:24px" viewBox="0 0 13 13"><rect width="13" height="13" rx="2" fill="#666"/><path d="M3 6.5h7M6.5 3v7" stroke="#fff" stroke-width="1.6"/></svg><div class="q" style="top:17px">Aliquam dignissim elit nec mauris porta?</div></div>
    <div class="abs qa" style="top:2037px;height:60px"><svg class="box" style="top:24px" viewBox="0 0 13 13"><rect width="13" height="13" rx="2" fill="#666"/><path d="M3 6.5h7M6.5 3v7" stroke="#fff" stroke-width="1.6"/></svg><div class="q" style="top:17px">Nulla porttitor nibh ut mi feugiat rhoncus quis in ante?</div></div>
    <div class="abs qa" style="top:2101px;height:60px"><svg class="box" style="top:24px" viewBox="0 0 13 13"><rect width="13" height="13" rx="2" fill="#666"/><path d="M3 6.5h7M6.5 3v7" stroke="#fff" stroke-width="1.6"/></svg><div class="q" style="top:17px">Nam tempus augue eu ante lacinia euismod sodales ligula porttitor?</div></div>
  </section>

  <footer class="abs footer">
    <div class="links">Assisted Living &nbsp;| &nbsp;Memory Care &nbsp;| &nbsp;Nursing Homes &nbsp;| &nbsp;More Living Options &nbsp;| &nbsp;Planning &amp; Advice &nbsp;| &nbsp;How Our Service Works</div>
    <div class="copy">Copyright © 2019 &nbsp;The Elder Nook. &nbsp;All rights reserved.</div>
    <span class="social" style="left:820px"></span>
    <span class="social" style="left:852px"></span>
  </footer>
</div>
</body>
</html>
```